Lake of the Ozarks Anniversary Flag

Looking for a flag design that incorporates the outline of the Lake of the Ozarks on a white background with some additional wording/ design incorporated. Would like the lake outline in Navy Blue. On the top of the flag "LAKE OF THE OZARKS" in all caps (possibly also in Navy Blue with a bright red outline. In the background, large and centered in subdued gray "90th." Bottom left corner "1931" and bottom right corner "2021." Possibly also add a compass somewhere (possibly in the void to the middle left area. This is a flag being designed for boats that is to commemorate the 90th anniversary of Lake of the Ozarks this year. I have a couple more lake outlines I have screenshotted but this website won't seem to download them. I can send them separate if that assists.

```html
<!DOCTYPE html>
<html lang="en">
<head>
<meta charset="utf-8">
<title>Lake of the Ozarks 90th Anniversary Flag</title>
<link rel="stylesheet" href="https://fonts.googleapis.com/css2?family=Archivo:wdth,wght@125,900&family=Graduate&display=swap">
<style>
  :root {
    --navy: #2b3990;
    --red: #ed1c24;
    --white: #ffffff;
    --gray-fill: #d1d2d4;
    --gray-edge: #9d9ea0;
    --lake-teal: #16999b;
  }
  html, body {
    margin: 0;
    padding: 0;
    width: 1200px;
    height: 716px;
    overflow: hidden;
    background: var(--white);
  }
  .flag {
    display: block;
    width: 1200px;
    height: 716px;
  }
  .stripe-navy { fill: var(--navy); }
  .stripe-red { fill: var(--red); }
  .varsity {
    font-family: "Graduate", serif;
    fill: var(--navy);
    stroke: var(--red);
    stroke-width: 6;
    paint-order: stroke fill;
    stroke-linejoin: round;
  }
  .title { font-size: 104px; }
  .year { font-size: 106px; }
  .anniversary {
    font-family: "Archivo", sans-serif;
    font-weight: 900;
    font-stretch: 125%;
  }
  .anniversary-shadow { fill: var(--gray-edge); }
  .anniversary-face {
    fill: var(--gray-fill);
    stroke: var(--gray-edge);
    stroke-width: 3;
  }
  .numeral { font-size: 430px; }
  .ordinal { font-size: 250px; }
  .compass-ring { fill: none; stroke: var(--navy); stroke-width: 1.5; }
  .compass-point { fill: var(--navy); }
  .compass-point-light { fill: var(--white); stroke: var(--navy); stroke-width: 1; }
  .compass-letter {
    font-family: "Graduate", serif;
    font-size: 14px;
    fill: var(--navy);
    text-anchor: middle;
  }
</style>
</head>
<body>
<svg class="flag" viewBox="0 0 1184 710" preserveAspectRatio="none" xmlns="http://www.w3.org/2000/svg">
  <defs>
    <radialGradient id="lake-tone" cx="50%" cy="50%" r="50%">
      <stop offset="0%" stop-color="#16999b" stop-opacity="0.55"/>
      <stop offset="70%" stop-color="#16999b" stop-opacity="0.3"/>
      <stop offset="100%" stop-color="#16999b" stop-opacity="0"/>
    </radialGradient>
  </defs>

  <rect class="background" width="1184" height="710" fill="#ffffff"/>

  <g class="border-top">
    <rect class="stripe-navy" x="0" y="0" width="1184" height="10"/>
    <rect class="stripe-red" x="0" y="16" width="1184" height="6"/>
  </g>

  <text class="varsity title" x="52" y="116" textLength="1080" lengthAdjust="spacingAndGlyphs">LAKE OF THE OZARKS</text>

  <g class="anniversary">
    <text class="anniversary-shadow numeral" x="44" y="526" textLength="740" lengthAdjust="spacingAndGlyphs">90</text>
    <text class="anniversary-face numeral" x="50" y="520" textLength="740" lengthAdjust="spacingAndGlyphs">90</text>
    <text class="anniversary-shadow ordinal" x="816" y="391" textLength="322" lengthAdjust="spacingAndGlyphs">th</text>
    <text class="anniversary-face ordinal" x="822" y="385" textLength="322" lengthAdjust="spacingAndGlyphs">th</text>
  </g>

  <ellipse class="lake-outline" role="img" aria-label="Outline map of Lake of the Ozarks in teal"
           cx="560" cy="400" rx="400" ry="290" fill="url(#lake-tone)"/>

  <g class="compass" transform="translate(1022 480)">
    <circle class="compass-ring" r="36"/>
    <circle class="compass-ring" r="30"/>
    <polygon class="compass-point" points="0,-48 6,-6 0,0"/>
    <polygon class="compass-point-light" points="0,-48 -6,-6 0,0"/>
    <polygon class="compass-point" points="0,48 -6,6 0,0"/>
    <polygon class="compass-point-light" points="0,48 6,6 0,0"/>
    <polygon class="compass-point" points="48,0 6,6 0,0"/>
    <polygon class="compass-point-light" points="48,0 6,-6 0,0"/>
    <polygon class="compass-point" points="-48,0 -6,-6 0,0"/>
    <polygon class="compass-point-light" points="-48,0 -6,6 0,0"/>
    <polygon class="compass-point" points="24,-24 4,0 0,0 0,-4"/>
    <polygon class="compass-point" points="-24,24 -4,0 0,0 0,4"/>
    <polygon class="compass-point" points="24,24 0,4 0,0 4,0"/>
    <polygon class="compass-point" points="-24,-24 0,-4 0,0 -4,0"/>
    <text class="compass-letter" x="0" y="-54">N</text>
    <text class="compass-letter" x="0" y="66">S</text>
    <text class="compass-letter" x="-56" y="5">W</text>
    <text class="compass-letter" x="55" y="5">E</text>
  </g>

  <text class="varsity year year-start" x="52" y="669" textLength="210" lengthAdjust="spacingAndGlyphs">1931</text>
  <text class="varsity year year-end" x="908" y="669" textLength="224" lengthAdjust="spacingAndGlyphs">2021</text>

  <g class="border-bottom">
    <rect class="stripe-red" x="0" y="685" width="1184" height="6"/>
    <rect class="stripe-navy" x="0" y="697" width="1184" height="13"/>
  </g>
</svg>
</body>
</html>
```